Custom Cabinet Shop Needs a website design

Hi,
We need a website for a Custom Cabinet Shop and Cabinet parts manufacturing business.
The business has two sides to it. One side provides custom Kitchens, vanities, entertainment units, offices and what not to homeowners and contractors.
The 2nd side of the business provides built to order cabinet boxes and other parts required to put together a project to other cabinet shops, small contractors looking to install there own cabinets.
Website will need a Gallery to display work.
Color scheme to go well with logo.
current website is www.brambleoakcustomcabinets.com
being changed to www.brambleoak.ca
Logo Included in attached files.
Tagline "Joinery with Spirit"
Mission Statement "Our passion is to deliver inspired cabinetry solutions to suit all your needs, supported by our phenomenal star class customer service"
The website should convey quality and professionalism.
Thank you.
Homeowners/ Contractors
Entertainment

```html
<!DOCTYPE html>
<html lang="en">
<head>
<meta charset="utf-8">
<title>Brambleoak Custom Cabinets</title>
<link href="https://fonts.googleapis.com/css2?family=Montserrat:wght@400;500;600;700&family=Open+Sans:wght@400;600&display=swap" rel="stylesheet">
<style>
:root{
  --orange:#f05a22;
  --charcoal:#231f20;
  --ink:#111;
  --muted:#555;
  --white:#fff;
  --rule:#c9c9c9;
}
*{box-sizing:border-box;margin:0;padding:0}
html,body{width:1200px;height:1101px;overflow:hidden;background:var(--white)}
body{position:relative;font-family:'Open Sans',sans-serif;color:var(--ink)}
.hero-photo{position:absolute;left:0;top:0;width:1200px;height:606px;
  background:linear-gradient(90deg,#3d362f 0%,#6b5a48 30%,#7a6655 55%,#4a3b2e 75%,#8e8a80 100%);}
.hero-shade{position:absolute;left:0;top:0;width:1200px;height:606px;
  background:linear-gradient(180deg,rgba(0,0,0,.15) 0%,rgba(0,0,0,.35) 60%,rgba(0,0,0,.7) 100%)}
.topbar-phone{position:absolute;right:175px;top:5px;color:var(--white);font:400 13px 'Montserrat',sans-serif;letter-spacing:.5px;display:flex;align-items:center;gap:5px}
.header{position:absolute;left:0;top:26px;width:1200px;height:74px;background:var(--white)}
.brand{position:absolute;left:178px;top:22px;display:flex;align-items:center;gap:8px;font:700 19px 'Montserrat',sans-serif;color:var(--charcoal);text-transform:uppercase;letter-spacing:.5px}
.brand-mark{width:16px;height:16px;background:var(--orange);border-radius:50%}
.nav{position:absolute;top:0;height:74px;display:flex;left:602px}
.nav a{display:flex;align-items:center;padding:0 7px;height:74px;font:400 10.5px 'Montserrat',sans-serif;color:var(--ink);text-decoration:none;text-transform:uppercase;white-space:nowrap}
.nav a.active{background:var(--orange);color:var(--white);padding:0 12px}
.nav-mail{position:absolute;left:1008px;top:31px}
.hero-title{position:absolute;left:0;top:202px;width:1200px;text-align:center;color:var(--white);font:500 40px 'Montserrat',sans-serif;text-transform:uppercase;letter-spacing:.5px}
.hero-lead{position:absolute;left:0;top:253px;width:1200px;text-align:center;color:var(--white);font-size:12.5px;line-height:15.5px}
.hero-social{position:absolute;left:534px;top:311px;display:flex;gap:9px}
.arrow{position:absolute;top:318px}
.cta{position:absolute;left:486px;top:390px}
.cta span{position:absolute;left:0;top:0;width:114px;height:24px;display:flex;align-items:center;justify-content:center;color:var(--white);font:400 9.5px 'Montserrat',sans-serif;text-transform:uppercase}
.more{position:absolute;left:621px;top:393px;display:flex;align-items:center;gap:5px;color:var(--white);font:400 12.5px 'Montserrat',sans-serif;letter-spacing:.8px}
.thumbs{position:absolute;left:373px;top:502px;display:flex;gap:3px}
.thumb{width:73px;height:51px}
.thumb.current{border:3px solid var(--white)}
.band{position:absolute;top:606px;height:158px}
.band-dark{left:0;width:601px;background:var(--charcoal)}
.band-orange{left:601px;width:599px;background:var(--orange)}
.band-circle{position:absolute;top:33px}
.band-copy{position:absolute;top:50px;color:var(--white);width:215px}
.band-copy h2{font:700 17.5px 'Montserrat',sans-serif;margin-bottom:3px;white-space:nowrap}
.band-copy p{font-size:10.5px;line-height:12.3px}
.band-copy a{color:var(--white)}
.pin{position:absolute;left:590px;top:824px}
.foot-social{position:absolute;left:558px;top:868px;display:flex;gap:2px}
.foot-nav{position:absolute;left:225px;top:919px;width:750px;height:33px;border-top:1px solid var(--rule);border-bottom:1px solid var(--rule);display:flex;justify-content:center;align-items:center;gap:15px}
.foot-nav a{font:400 10px 'Montserrat',sans-serif;color:var(--muted);text-decoration:none;text-transform:uppercase}
.foot-about{position:absolute;left:250px;top:971px;width:700px;text-align:center;font-size:10.5px;line-height:12px;color:#444}
.foot-about a{color:var(--orange);text-decoration:none}
.copyright{position:absolute;left:0;top:1027px;width:1200px;text-align:center;font-size:10.5px;color:#444}
</style>
</head>
<body>
<div class="hero-photo" role="img" aria-label="Photograph of a finished custom kitchen with stainless appliances, granite island and bar stools"></div>
<div class="hero-shade"></div>

<div class="topbar-phone">
  <svg width="9" height="11" viewBox="0 0 9 11"><path d="M2 0 L3.5 2.5 L2.5 3.6 Q3.5 6.5 5.6 8 L6.8 7 L9 8.8 L7.6 10.6 Q2.5 9.5 0.4 1.6 Z" fill="#fff"/></svg>
  555-014-2160
</div>

<header class="header">
  <div class="brand"><span class="brand-mark"></span>Brambleoak</div>
  <nav class="nav">
    <a href="#">Home</a>
    <a href="#" class="active">About</a>
    <a href="#">Gallery</a>
    <a href="#">Services</a>
    <a href="#">Warranty</a>
    <a href="#">Contact</a>
  </nav>
  <svg class="nav-mail" width="17" height="12" viewBox="0 0 17 12"><rect x=".5" y=".5" width="16" height="11" fill="none" stroke="#f05a22"/><path d="M.5 .5 L8.5 7 L16.5 .5 M.5 11.5 L6.5 5.5 M16.5 11.5 L10.5 5.5" fill="none" stroke="#f05a22"/></svg>
</header>

<h1 class="hero-title">Joinery with Spirit</h1>
<p class="hero-lead">Our passion is to deliver inspired cabinetry solutions to suit all your needs,<br>supported by our phenomenal star class customer service</p>

<div class="hero-social" aria-label="Social links">
  <svg width="38" height="42" viewBox="0 0 38 42"><path d="M19 1 L37 11 L37 31 L19 41 L1 31 L1 11 Z" fill="none" stroke="#fff" stroke-width="1.3"/><circle cx="19" cy="21" r="7" fill="none" stroke="#fff" stroke-width="1.6"/><path d="M12 21 H26 M19 14 Q15 21 19 28 Q23 21 19 14" fill="none" stroke="#fff" stroke-width="1.2"/></svg>
  <svg width="38" height="42" viewBox="0 0 38 42"><path d="M19 1 L37 11 L37 31 L19 41 L1 31 L1 11 Z" fill="none" stroke="#fff" stroke-width="1.3"/><path d="M11 15 H27 V25 H17 L13 29 V25 H11 Z" fill="#fff"/></svg>
  <svg width="38" height="42" viewBox="0 0 38 42"><path d="M19 1 L37 11 L37 31 L19 41 L1 31 L1 11 Z" fill="none" stroke="#fff" stroke-width="1.3"/><path d="M14 21 L24 15 M14 21 L24 27" stroke="#fff" stroke-width="1.4"/><circle cx="14" cy="21" r="2.6" fill="#fff"/><circle cx="24" cy="15" r="2.6" fill="#fff"/><circle cx="24" cy="27" r="2.6" fill="#fff"/></svg>
</div>

<svg class="arrow" style="left:150px" width="24" height="40" viewBox="0 0 24 40"><path d="M22 2 L3 20 L22 38" fill="none" stroke="rgba(255,255,255,.55)" stroke-width="2"/></svg>
<svg class="arrow" style="left:1026px" width="24" height="40" viewBox="0 0 24 40"><path d="M2 2 L21 20 L2 38" fill="none" stroke="rgba(255,255,255,.55)" stroke-width="2"/></svg>

<div class="cta">
  <svg width="114" height="24" viewBox="0 0 114 24"><path d="M1 1 H113 L107 12 L113 23 H1 L7 12 Z" fill="rgba(0,0,0,.2)" stroke="#fff" stroke-width="1.3"/></svg>
  <span>Call to action</span>
</div>
<div class="more">
  <svg width="10" height="10" viewBox="0 0 10 10"><circle cx="5" cy="5" r="5" fill="#fff"/><path d="M4 2.8 L6.2 5 L4 7.2" fill="none" stroke="#222" stroke-width="1.3"/></svg>
  Learn More
</div>

<div class="thumbs">
  <div class="thumb" style="background:#4a4440" role="img" aria-label="Gallery thumbnail: kitchen cabinetry"></div>
  <div class="thumb current" style="background:#6b5444" role="img" aria-label="Gallery thumbnail: kitchen island with stools"></div>
  <div class="thumb" style="background:#4e3a28" role="img" aria-label="Gallery thumbnail: dark wood kitchen"></div>
  <div class="thumb" style="background:#766a5c" role="img" aria-label="Gallery thumbnail: bright kitchen with windows"></div>
  <div class="thumb" style="background:#3a2e2c" role="img" aria-label="Gallery thumbnail: kitchen with pendant lights"></div>
  <div class="thumb" style="background:#54463c" role="img" aria-label="Gallery thumbnail: long kitchen island"></div>
</div>

<section class="band band-dark">
  <svg class="band-circle" style="left:224px" width="92" height="92" viewBox="0 0 92 92"><circle cx="46" cy="46" r="45" fill="none" stroke="#fff" stroke-width="1"/><g fill="none" stroke="#fff" stroke-width="1.2"><path d="M24 66 L46 40 L50 44 L28 70 Q24 70 24 66 Z"/><path d="M44 32 L56 28 L64 38 L58 48 L48 38 Z"/></g></svg>
  <div class="band-copy" style="left:339px">
    <h2>One Side Provides</h2>
    <p>Custom kitchens, vanities and units for homeowners and contractors built to last. <a href="#">Learn More</a></p>
  </div>
</section>
<section class="band band-orange">
  <svg class="band-circle" style="left:67px" width="92" height="92" viewBox="0 0 92 92"><circle cx="46" cy="46" r="45" fill="none" stroke="#fff" stroke-width="1"/><g fill="none" stroke="#fff" stroke-width="1.2"><path d="M24 68 L28 58 L58 28 L64 34 L34 64 Z"/><path d="M30 30 L36 24 L68 56 L62 62 Z"/></g></svg>
  <div class="band-copy" style="left:178px">
    <h2>Second Side Provides</h2>
    <p>Built to order cabinet boxes and parts for cabinet shops and contractors. <a href="#">Learn More</a></p>
  </div>
</section>

<svg class="pin" width="20" height="24" viewBox="0 0 20 24"><path d="M10 24 Q1 13 1 9 A9 9 0 0 1 19 9 Q19 13 10 24 Z" fill="#f05a22"/><circle cx="10" cy="9" r="3.5" fill="#fff"/></svg>

<div class="foot-social" aria-label="Social links">
  <svg width="20" height="22" viewBox="0 0 20 22"><path d="M10 1 L19 6 L19 16 L10 21 L1 16 L1 6 Z" fill="none" stroke="#333"/><circle cx="10" cy="11" r="3.5" fill="none" stroke="#333"/><path d="M6.5 11 H13.5" stroke="#333" stroke-width=".8"/></svg>
  <svg width="20" height="22" viewBox="0 0 20 22"><path d="M10 1 L19 6 L19 16 L10 21 L1 16 L1 6 Z" fill="none" stroke="#333"/><path d="M6 8 H14 V13 H9 L7 15 V13 H6 Z" fill="#333"/></svg>
  <svg width="20" height="22" viewBox="0 0 20 22"><path d="M10 1 L19 6 L19 16 L10 21 L1 16 L1 6 Z" fill="none" stroke="#333"/><path d="M7 11 L13 8 M7 11 L13 14" stroke="#333" stroke-width=".9"/><circle cx="7" cy="11" r="1.5" fill="#333"/><circle cx="13" cy="8" r="1.5" fill="#333"/><circle cx="13" cy="14" r="1.5" fill="#333"/></svg>
  <svg width="20" height="22" viewBox="0 0 20 22"><path d="M10 1 L19 6 L19 16 L10 21 L1 16 L1 6 Z" fill="none" stroke="#333"/><rect x="6" y="8" width="8" height="6" fill="#333"/><path d="M6 8 L10 11 L14 8" fill="none" stroke="#fff" stroke-width=".8"/></svg>
</div>

<nav class="foot-nav">
  <a href="#">Home</a><a href="#">About</a><a href="#">Gallery</a><a href="#">Services</a><a href="#">Warranty</a><a href="#">Contact</a>
</nav>
<p class="foot-about">About text lorem ipsum dolor sit amet, consectetur adipisicing elit, sed do eiusmod tempor incididunt ut labore et dolore magna aliqua. Ut enim ad minim veniam, quis nostrud exercitation ullamco nisi ut aliquip ex ea commodo consequat. Duis aute irure dolor in reprehenderit in voluptate velit esse cillum dolore eu fugiat nulla pariatur. Excepteur sint occaecat cupidatat non <a href="#">Learn More</a></p>
<p class="copyright">© 2015</p>
</body>
</html>
```